Meridale Staffing Website

My business has been word of mouth over the last 3 years and has grown. Now I need a website for additional marketing as we have new clients asking for a website.

You have already completed my Logo during an earlier project. I have attached the logo.

We do Staff Augmentation and Operation Support.

What is that?
Staff augmentation is an outsourcing strategy that allows companies to fill specific, temporary roles to achieve business objectives. This staffing method complements existing teams with specific talent, enhancing business capabilities or filling gaps left by members on extended leave.

We work alongside the internal recruiting team to assist clients to meet and exceed financial goals.

```html
<!DOCTYPE html>
<html lang="en">
<head>
<meta charset="utf-8">
<title>Meridale Staffing</title>
<link href="https://fonts.googleapis.com/css2?family=Montserrat:wght@400;500;600&display=swap" rel="stylesheet">
<style>
:root{
  --navy:#0f3f6e;
  --blue:#1d5a93;
  --deep:#0b2a4a;
  --ink:#111418;
  --text:#5d636b;
  --white:#ffffff;
  --line:#c9ced4;
}
*{box-sizing:border-box;margin:0;padding:0}
html,body{width:1200px;height:3186px;overflow:hidden}
body{font-family:'Montserrat',sans-serif;background:var(--white);position:relative;color:var(--text)}
section,header,footer{position:absolute;left:0;width:1200px}
.btn{display:inline-block;font-size:15px;font-weight:500;color:var(--white);padding:9px 13px;border-radius:3px;text-transform:uppercase}
.btn-solid{background:var(--navy)}
.btn-outline{border:1.5px solid var(--white)}
.eyebrow{font-size:18px;letter-spacing:5px;text-transform:uppercase}
.title{font-size:41px;font-weight:500;margin-top:6px}
.rule{width:137px;height:2px;margin:18px 0 30px}
/* header */
.site-header{top:0;height:90px;background:var(--ink)}
.brand{position:absolute;left:112px;top:26px;display:flex;align-items:center;gap:10px;color:var(--blue);font-size:20px;font-weight:600}
.brand-dot{width:34px;height:34px;border-radius:50%;background:var(--blue)}
.main-nav{position:absolute;left:420px;top:0;display:flex;height:90px}
.main-nav a{color:var(--white);font-size:13px;font-weight:500;padding:40px 17px 0;height:90px}
.main-nav a.active{color:var(--blue);position:relative}
.main-nav a.active::after{content:"";position:absolute;left:0;right:0;top:56px;height:34px;background:var(--navy)}
.cta{position:absolute;left:965px;top:29px;background:var(--navy);color:var(--white);font-size:14px;font-weight:500;padding:9px 17px;border-radius:3px}
/* hero */
.hero{top:90px;height:587px;background:linear-gradient(180deg,#2b4e78 0%,#1f3e66 45%,#162c4d 100%);text-align:center;color:var(--white)}
.hero h1{margin-top:220px;font-size:56px;font-weight:500}
.hero p{font-size:27px;margin-top:6px}
.hero .btn{margin-top:26px;font-size:15px;padding:11px 24px;border:1.5px solid var(--white);border-radius:3px}
.dots{margin-top:28px;display:flex;justify-content:center;gap:6px}
.dots span{width:14px;height:14px;border-radius:50%;border:2px solid var(--white)}
.dots span.on{background:var(--blue);border-color:var(--blue)}
/* about */
.about{top:677px;height:537px}
.about-copy{position:absolute;left:111px;top:69px;width:475px}
.about-copy .eyebrow{color:#333}
.about-copy .title{color:var(--navy)}
.about-copy .rule{background:var(--navy)}
.about-copy p{font-size:13px;line-height:20.5px;margin-bottom:20px;text-align:justify}
.about-media{position:absolute;left:601px;top:0;width:599px;height:537px;background:linear-gradient(135deg,#0d4a86,#1a5f9e 55%,#0a3d72)}
/* services */
.services{top:1214px;height:591px}
.svc{position:absolute;top:0;width:600px;height:591px;color:var(--white);padding:119px 0 0 111px}
.svc-a{left:0;background:linear-gradient(135deg,#153659,#0e2a48 60%,#12304f)}
.svc-b{left:601px;background:linear-gradient(135deg,#2a2b2e,#1b1c1f 60%,#222326);padding-left:50px}
.svc .rule{background:var(--white)}
.svc p{font-size:13px;line-height:20.5px;width:440px;margin-bottom:20px;text-align:justify}
.svc .btn{margin-top:44px}
/* why */
.why{top:1805px;height:532px}
.why-media{position:absolute;left:0;top:0;width:600px;height:532px;background:linear-gradient(180deg,#e2e7ea,#cdd5da)}
.why-copy{position:absolute;left:619px;top:64px;width:475px}
.why-copy .eyebrow{color:#333}
.why-copy .title{color:var(--navy)}
.why-copy .rule{background:var(--navy);margin-bottom:22px}
.why-copy p{font-size:16px;line-height:23px;margin-bottom:23px;text-align:justify}
/* contact */
.contact{top:2337px;height:378px;background:var(--navy);text-align:center;color:var(--white)}
.contact h2{font-size:39px;font-weight:500;margin-top:64px}
.contact p{font-size:16px;line-height:27px;width:760px;margin:12px auto 0}
.site-footer{top:2715px;height:471px;background:linear-gradient(180deg,#182433,#0f1822)}
.quote-card{position:absolute;left:120px;top:2531px;width:977px;height:413px;background:var(--white);border-bottom:3px solid var(--navy)}
.quote-icon{position:absolute;left:36px;top:40px}
.quote-head{position:absolute;left:121px;top:32px}
.quote-head .eyebrow{color:var(--navy);font-size:21px;letter-spacing:4px}
.quote-head h3{color:var(--navy);font-size:30px;font-weight:600;margin-top:2px}
.quote-lead{position:absolute;left:36px;top:122px;font-size:16px;line-height:23px;width:410px}
.info{position:absolute;left:36px;font-size:16px;color:#333;display:flex;gap:14px}
.info small{display:block;font-size:14px;line-height:26px}
.form{position:absolute;left:480px;top:39px;width:462px}
.field{position:absolute;border:1px solid var(--line);height:42px;font-size:12px;color:#999;padding:13px 16px}
.submit{position:absolute;left:0;top:279px;width:225px;height:52px;background:var(--navy);color:var(--white);font-size:19px;letter-spacing:4px;text-align:center;line-height:52px;border-radius:2px}
.socials{position:absolute;top:3028px;left:0;width:1200px;display:flex;justify-content:center;gap:22px}
.socials span{width:18px;height:18px;border-radius:50%;background:var(--blue)}
.foot-nav{position:absolute;top:3066px;left:0;width:1200px;display:flex;justify-content:center;gap:34px;font-size:13px;font-weight:500;color:var(--white)}
.copyright{position:absolute;top:3106px;width:1200px;text-align:center;font-size:12px;color:var(--white)}
</style>
</head>
<body>
<header class="site-header">
  <div class="brand"><span class="brand-dot"></span>Meridale Staffing</div>
  <nav class="main-nav">
    <a class="active">HOME</a><a>ABOUT</a><a>SERVICES</a><a>OUR TEAM</a><a>BLOG</a><a>CONTACT</a>
  </nav>
  <a class="cta">GE STARTED</a>
</header>

<section class="hero" role="img" aria-label="Photo of a business meeting in blue lounge chairs, blue tint">
  <h1>MERIDALE STAFFING</h1>
  <p>Skilled people, placed right where your team needs them</p>
  <a class="btn">LEARN MORE</a>
  <div class="dots"><span class="on"></span><span></span><span></span></div>
</section>

<section class="about">
  <div class="about-copy">
    <div class="eyebrow">About</div>
    <h2 class="title">Meridale Staffing</h2>
    <div class="rule"></div>
    <p>Sed ut perspiciatis unde omnis iste natus error sit voluptatem accusantium doloremque laudantium, totam rem aperiam, eaque ipsa quae ab illo inventore veritatis et quasi architecto beatae vitae dicta sunt explicabo. Nemo enim ipsam voluptatem quia voluptas sit aspernatur aut odit aut fugit, sed quia consequuntur magni dolores eos qui ratione voluptatem sequi nesciunt.</p>
    <p>Neque porro quisquam est, qui dolorem ipsum quia dolor sit amet, consectetur, adipisci velit, sed quia non numquam eius modi tempora incidunt ut labore et dolore magnam aliquam quaerat voluptatem. Ut enim ad minima veniam, quis nostrum exercitationem ullam corporis suscipit laboriosam, nisi ut aliquid ex ea commodi consequatur?</p>
    <a class="btn btn-solid">LEARN MORE</a>
  </div>
  <div class="about-media" role="img" aria-label="Photo of colleagues working at a computer, deep blue overlay"></div>
</section>

<section class="services">
  <div class="svc svc-a" role="img" aria-label="Photo of a team at work behind navy overlay">
    <div class="eyebrow">Services</div>
    <h2 class="title">Staff Augmentation</h2>
    <div class="rule"></div>
    <p>Sed ut perspiciatis unde omnis iste natus error sit voluptatem accusantium doloremque laudantium, totam rem aperiam, eaque ipsa quae ab illo inventore veritatis et quasi architecto beatae vitae dicta sunt explicabo. Nemo enim ipsam voluptatem quia voluptas</p>
    <p>Neque porro quisquam est, qui dolorem ipsum quia dolor sit amet, consectetur, adipisci velit, sed quia non numquamad</p>
    <a class="btn btn-outline">LEARN MORE</a>
  </div>
  <div class="svc svc-b" role="img" aria-label="Photo of a professional at a desk behind dark overlay">
    <div class="eyebrow">Services</div>
    <h2 class="title">Operation Support</h2>
    <div class="rule"></div>
    <p>Sed ut perspiciatis unde omnis iste natus error sit voluptatem accusantium doloremque laudantium, totam rem aperiam, eaque ipsa quae ab illo inventore veritatis et quasi architecto beatae vitae dicta sunt explicabo. Nemo enim ipsam voluptatem quia voluptas</p>
    <p>Neque porro quisquam est, qui dolorem ipsum quia dolor sit amet, consectetur, adipisci velit, sed quia non numquamad</p>
    <a class="btn btn-outline">LEARN MORE</a>
  </div>
</section>

<section class="why">
  <div class="why-media" role="img" aria-label="Photo of four job candidates seated in a row holding documents"></div>
  <div class="why-copy">
    <div class="eyebrow">Why Choose Us</div>
    <h2 class="title">Meridale Staffing</h2>
    <div class="rule"></div>
    <p>Staff augmentation is an outsourcing strategy that allows companies to fill specific, temporary roles to achieve business objectives.</p>
    <p>This staffing method complements existing teams with specific talent, enhancing business capabilities or filling gaps left by members on extended leave.</p>
    <p>We work alongside the internal recruiting team to assist clients to meet and exceed financial goals.</p>
    <a class="btn btn-solid">LEARN MORE</a>
  </div>
</section>

<section class="contact">
  <h2>Contact Us</h2>
  <p>Lorem Ipsum is simply dummy text of the printing and typesetting industry. Lorem Ipsum has been the industry's standard dummy text ever since the 1500s, when</p>
</section>

<footer class="site-footer" role="img" aria-label="Photo of a group of colleagues, dark blue overlay"></footer>

<div class="quote-card">
  <svg class="quote-icon" width="48" height="50" viewBox="0 0 48 50" aria-hidden="true">
    <rect x="8" y="2" width="32" height="30" fill="none" stroke="#0f3f6e" stroke-width="3"/>
    <path d="M14 10h20M14 16h20M14 22h14" stroke="#0f3f6e" stroke-width="3"/>
    <path d="M2 20v28h44V20L24 36z" fill="#0f3f6e"/>
  </svg>
  <div class="quote-head">
    <div class="eyebrow">Get In Touch</div>
    <h3>Request A Quote</h3>
  </div>
  <p class="quote-lead">Neque porro quisquam est qui dolorem ipsum quia dolor sit amet, consectetur, adipisci velit...</p>
  <div class="info" style="top:190px">
    <svg width="20" height="16" viewBox="0 0 20 16" aria-hidden="true"><path d="M1 3l6-2 6 2 6-2v12l-6 2-6-2-6 2z M7 1v12M13 3v12" fill="none" stroke="#222" stroke-width="1.6"/></svg>
    <div>Meridale Staffing<small>Finibus Bonorum et,</small><small>Sed ut perspiciatis unde omnis</small></div>
  </div>
  <div class="info" style="top:292px">
    <svg width="18" height="18" viewBox="0 0 24 24" aria-hidden="true"><path d="M6.6 10.8a15 15 0 0 0 6.6 6.6l2.2-2.2c.3-.3.7-.4 1-.2 1.1.4 2.3.6 3.6.6.6 0 1 .4 1 1V20c0 .6-.4 1-1 1A17 17 0 0 1 3 4c0-.6.4-1 1-1h3.5c.6 0 1 .4 1 1 0 1.3.2 2.5.6 3.6.1.3 0 .7-.2 1z" fill="#222"/></svg>
    <div>Phone: +(555) 201 4418</div>
  </div>
  <div class="info" style="top:340px">
    <svg width="18" height="14" viewBox="0 0 18 14" aria-hidden="true"><rect x="0" y="0" width="18" height="14" fill="#222"/><path d="M0 0l9 7 9-7" fill="none" stroke="#fff" stroke-width="1.5"/></svg>
    <div>E-mail: hello@meridalestaffing.com</div>
  </div>
  <div class="form">
    <div class="field" style="left:0;top:0;width:228px">Name</div>
    <div class="field" style="left:234px;top:0;width:228px">Phone</div>
    <div class="field" style="left:0;top:68px;width:228px">Email</div>
    <div class="field" style="left:234px;top:68px;width:228px">Select Your Services
      <svg style="position:absolute;right:10px;top:16px" width="16" height="9" viewBox="0 0 16 9" aria-hidden="true"><path d="M0 0h16L8 9z" fill="#111"/></svg>
    </div>
    <div class="field" style="left:0;top:136px;width:462px;height:114px">Your Message Here</div>
    <div class="submit">SUBMIT NOW</div>
  </div>
</div>

<div class="socials" aria-label="Social links"><span></span><span></span><span></span><span></span><span></span></div>
<nav class="foot-nav"><span>HOME</span><span>ABOUT</span><span>SERVICES</span><span>OUR TEAM</span><span>BLOG</span><span>CONTACT</span></nav>
<div class="copyright">Meridale Staffing © 2022 . All Rights Reserved.</div>
</body>
</html>
```